High-end executive coaching group needs a 2 page digital flyer

We need a 2 page digital flyer for a high end leadership coaching offering for global leaders in healthcare. The flyer will advertise a new service (an elite senior leadership coaching group) for senior leaders in the healthcare industry from around the world.
The flyer should be upmarket, professional and minimalist in style to meet the expectations of my professional market (very senior doctors and executives).
The design should be based on my existing logo and brand, see my landing page: www.marlowadvisory.com
The key elements needed are
1) An editable PDF which we can update as we revise the specific details of the offering. The text and draft design for this is attached.
2) The banner image should be high quality but abstract. It can be based on the landing page of my website (the two ripple effects) but does not need to strictly adhere to this.
3) The logo placement of the Marlow Advisory delta sign should be discreet so that it does not dominate
4) The small logos of our professional accrediting organisations should be discreetly placed at the end and should not dominate. They might work best as mono icons in a footer (e.g. blue on a white background, or white on blue.
5) Please find enclosed a previous flyer as an example of a similar style we have used for more junior professionals. The design worked quite well, although we now need a more upmarket version for our senior executives.

Please note this design specifically needs to use existing branding and images from my website: marlowadvisory.com. We are definitely not looking for stock "leadership team" images for this high-end brochure.

Target Market(s)

Senior global leaders in the healthcare industry

Industry/Entity Type

Leading business schools & Healthcare industry.

Font styles to use
Other font styles liked:
• Operetta (selective use for heading) and Sofia Pro (body text)

Colors
0054AA
0677BA
7BADD7
CADEEF
E8F1F8

Requirements
Must have
• Clean minimalist and high professionally look that directly speaks to the interests and perspectives of senior leader leaders in healthcare. It also needs very clear call to action sections
Nice to have
• Effective presentation of the two bios and photographs. These need to look impressive, but should not dominate.
Should not have
• Loud and bold colours, large use of logos.

```html
<!DOCTYPE html>
<html lang="en">
<head>
<meta charset="utf-8">
<title>Marlow Advisory – Senior Leadership Coaching Flyer</title>
<link rel="stylesheet" href="https://fonts.googleapis.com/css2?family=Playfair+Display:wght@600;700&family=Montserrat:wght@400;500;600;700&display=swap">
<style>
:root{
  --navy:#1f3a8f;
  --blue:#0054aa;
  --mid:#0677ba;
  --sky:#7badd7;
  --pale:#cadeef;
  --mist:#e8f1f8;
  --ink:#1d2b4a;
  --grey:#5b6577;
  --bg:#ffffff;
  --head:'Playfair Display', Georgia, serif;
  --body:'Montserrat', Arial, sans-serif;
}
*{box-sizing:border-box;margin:0;padding:0}
html,body{width:818px;height:1200px;overflow:hidden;background:var(--bg);font-family:var(--body);color:var(--ink)}
.canvas{position:relative;width:818px;height:1200px}
.page{position:absolute;top:320px;width:385px;height:548px;background:#fff;box-shadow:0 2px 10px rgba(20,40,90,.18);overflow:hidden}
.page--front{left:16px}
.page--back{left:417px}
.brand{position:absolute;top:16px;right:18px;display:flex;align-items:center;gap:5px;font-family:var(--head);font-weight:700;color:var(--navy);font-size:13px;line-height:1}
.brand__mark{width:9px;height:9px;background:var(--sky)}
.headline{position:absolute;left:20px;top:52px;font-family:var(--head);color:var(--navy);font-size:20px;line-height:1.05;font-weight:700;letter-spacing:.3px}
.headline span{display:block;color:var(--mid);font-size:26px}
.hero{position:absolute;left:160px;top:44px;width:225px;height:150px;background:linear-gradient(135deg,#c9d4e0,#8ea3bb 55%,#5d7391)}
.intro{position:absolute;left:0;top:140px;width:170px;background:var(--navy);color:#fff;padding:10px 12px 10px 20px;font-size:5.6px;line-height:1.45}
.intro strong{display:block;font-size:6.4px;margin-bottom:3px}
.wave{position:absolute;left:0;top:205px;width:385px;height:20px}
.benefits{position:absolute;left:20px;top:232px;width:150px}
.label{font-size:6.4px;font-weight:700;color:#fff;background:var(--mid);padding:3px 6px;display:inline-block;margin-bottom:6px}
.benefit{display:flex;gap:5px;margin-bottom:6px;font-size:5.2px;line-height:1.4;color:var(--grey)}
.benefit b{display:block;color:var(--blue);font-size:5.8px}
.tick{flex:none;width:8px;height:8px;border-radius:50%;background:var(--sky);position:relative}
.tick:after{content:"";position:absolute;left:2.5px;top:1.3px;width:2px;height:4px;border:solid #fff;border-width:0 1px 1px 0;transform:rotate(45deg)}
.quote{position:absolute;left:190px;top:230px;width:176px;font-size:5.6px;line-height:1.5;color:var(--grey);font-style:italic}
.quote__mark{font-family:var(--head);color:var(--sky);font-size:22px;line-height:.6;font-style:normal;display:block}
.schedule{position:absolute;left:190px;top:290px;width:176px;border-collapse:collapse;font-size:5.2px}
.schedule td{border:.5px solid var(--pale);padding:3px 4px}
.schedule td:first-child{background:var(--blue);color:#fff;font-weight:600;width:58px}
.schedule tr:nth-child(even) td:last-child{background:var(--mist)}
.price{position:absolute;left:190px;top:368px;display:flex;gap:4px}
.price span{background:var(--navy);color:#fff;font-size:6px;font-weight:700;padding:3px 6px}
.price span+span{background:var(--mist);color:var(--navy)}
.cta{position:absolute;left:190px;top:392px;width:176px;font-size:6.4px;font-weight:700;color:var(--blue);line-height:1.35}
.contact{position:absolute;left:190px;top:426px;font-size:5.6px;color:var(--grey)}
.contact h3{font-size:7px;color:var(--navy);margin-bottom:4px}
.contact p{display:flex;align-items:center;gap:4px;margin-bottom:3px}
.contact svg{width:7px;height:7px}
.footer-band{position:absolute;left:0;bottom:0;width:100%;height:34px;background:var(--navy);color:#fff;font-size:8px;font-weight:600;padding-left:20px;display:flex;align-items:center;letter-spacing:.4px}
.footer-band:before{content:"";position:absolute;right:0;top:-10px;width:160px;height:10px;background:var(--mid)}
/* back page */
.back-title{position:absolute;left:20px;top:18px;width:220px;font-family:var(--head);color:var(--navy);font-size:13px;line-height:1.2;font-weight:700}
.back-title small{display:block;font-family:var(--body);font-size:6px;color:var(--mid);font-weight:600;margin-top:3px}
.bio{position:absolute;left:20px;width:345px;display:flex;gap:12px;align-items:flex-start}
.bio--one{top:78px}
.bio--two{top:178px;flex-direction:row-reverse}
.portrait{flex:none;width:66px;height:66px;border-radius:50%;border:3px solid var(--pale);background:radial-gradient(circle at 50% 40%,#c8ccd4,#7c8797)}
.bio__text{font-size:5.3px;line-height:1.5;color:var(--grey)}
.bio__name{font-size:8px;font-weight:700;color:var(--blue)}
.bio__role{font-size:5.8px;color:var(--mid);font-weight:600;margin-bottom:3px}
.bio__quote{margin-top:4px;background:var(--mist);padding:4px 6px;font-style:italic;color:var(--navy);border-left:2px solid var(--sky)}
.engage{position:absolute;left:20px;top:282px;width:345px;font-size:7px;font-weight:700;color:var(--navy)}
.engage small{display:block;font-size:5.4px;font-weight:500;color:var(--grey);margin-top:2px}
.features{position:absolute;left:20px;top:310px;width:345px;display:flex;gap:8px}
.feature{flex:1;background:var(--mist);border-top:3px solid var(--mid);padding:7px;font-size:5.2px;line-height:1.45;color:var(--grey);height:62px}
.feature b{display:block;color:var(--blue);font-size:6px;margin-bottom:2px}
.book{position:absolute;left:20px;top:390px;width:345px;display:flex;justify-content:space-between}
.book__col{width:160px;font-size:5.4px;color:var(--grey);line-height:1.5}
.book__col h4{font-size:8px;color:var(--navy);margin-bottom:3px}
.button{display:inline-block;margin-top:4px;background:var(--blue);color:#fff;font-weight:700;font-size:5.8px;padding:3px 8px}
.accreditations{position:absolute;left:0;bottom:0;width:100%;height:44px;background:var(--mist);display:flex;align-items:center;justify-content:center;gap:14px}
.badge{width:34px;height:18px;background:var(--sky);opacity:.8}
.badge--round{width:20px;height:20px;border-radius:50%}
</style>
</head>
<body>
<main class="canvas">

  <section class="page page--front" aria-label="Flyer page one">
    <div class="hero" role="img" aria-label="Photograph of a coaching session with a group of seated leaders"></div>
    <div class="brand"><span class="brand__mark"></span>Marlow Advisory</div>
    <h1 class="headline">ELEVATE AND<br>IGNITE YOUR<span>LEADERSHIP</span></h1>
    <div class="intro">
      <strong>Transformational coaching for senior healthcare leaders</strong>
      A confidential peer group for physicians and executives who lead complex organisations across the globe. Sharpen your judgement, expand your influence and lead change with clarity.
    </div>
    <svg class="wave" viewBox="0 0 385 20" preserveAspectRatio="none" aria-hidden="true">
      <path d="M0 0 H170 Q220 20 385 6 V0 Z" fill="#cadeef"/>
    </svg>
    <div class="benefits">
      <span class="label">Programme benefits</span>
      <div class="benefit"><span class="tick"></span><p><b>Strategic clarity</b>Define priorities and lead with confident purpose.</p></div>
      <div class="benefit"><span class="tick"></span><p><b>Peer insight</b>Learn alongside senior leaders facing similar challenges.</p></div>
      <div class="benefit"><span class="tick"></span><p><b>Executive presence</b>Strengthen influence with boards and teams.</p></div>
      <div class="benefit"><span class="tick"></span><p><b>Resilient leadership</b>Sustain energy and wellbeing under pressure.</p></div>
      <div class="benefit"><span class="tick"></span><p><b>Lasting impact</b>Turn insight into measurable organisational change.</p></div>
    </div>
    <p class="quote"><span class="quote__mark">“</span>The group gave me space to step back, think clearly and return to my organisation with renewed direction and confidence.</p>
    <table class="schedule">
      <tr><td>Format</td><td>Six live virtual sessions, small cohort</td></tr>
      <tr><td>Duration</td><td>Six months, monthly ninety minutes</td></tr>
      <tr><td>Start date</td><td>Cohort opens early next quarter</td></tr>
      <tr><td>Group size</td><td>Maximum of eight senior leaders</td></tr>
      <tr><td>Includes</td><td>One private coaching session each</td></tr>
    </table>
    <div class="price"><span>Investment</span><span>On request</span></div>
    <p class="cta">Reserve your place now and ignite the leadership potential within you.</p>
    <div class="contact">
      <h3>Contact us</h3>
      <p><svg viewBox="0 0 10 10"><path d="M2 1 L4 1 L5 3.5 L3.8 4.5 Q4.8 6.2 5.5 6.2 L6.5 5 L9 6 L9 8 Q5 9.5 1 3 Z" fill="#0677ba"/></svg>+44 20 7946 0321</p>
      <p><svg viewBox="0 0 10 10"><rect x="1" y="2" width="8" height="6" fill="none" stroke="#0677ba"/><path d="M1 2 L5 5.5 L9 2" fill="none" stroke="#0677ba"/></svg>hello@marlowadvisory.com</p>
    </div>
    <div class="footer-band">www.marlowadvisory.com</div>
  </section>

  <section class="page page--back" aria-label="Flyer page two">
    <h2 class="back-title">Expertly guided by insights, academic rigour and practical leadership strategies<small>Meet your coaches</small></h2>
    <div class="brand"><span class="brand__mark"></span>Marlow Advisory</div>
    <article class="bio bio--one">
      <div class="portrait" role="img" aria-label="Portrait photograph of coach Daniel Harrow"></div>
      <div class="bio__text">
        <p class="bio__name">Daniel Harrow</p>
        <p class="bio__role">Professor, Executive Coach</p>
        <p>Daniel has advised hospital chiefs and health ministries for two decades, combining research in organisational behaviour with hands-on coaching for senior clinicians.</p>
        <p class="bio__quote">“Great leaders create the conditions for others to thrive.”</p>
      </div>
    </article>
    <article class="bio bio--two">
      <div class="portrait" role="img" aria-label="Portrait photograph of coach Dr Elena Varga"></div>
      <div class="bio__text">
        <p class="bio__name">Dr Elena Varga</p>
        <p class="bio__role">Psychotherapist, Leadership Advisor</p>
        <p>Elena supports senior doctors and executives to navigate complexity, build resilient teams and lead with empathy through periods of significant change.</p>
        <p class="bio__quote">“Self-awareness is the foundation of lasting influence.”</p>
      </div>
    </article>
    <p class="engage">Engage with global leaders, gain diverse insights and forge lasting bonds<small>A trusted circle of peers across health systems worldwide.</small></p>
    <div class="features">
      <div class="feature"><b>Global network</b>Connect with leaders from many countries and care settings.</div>
      <div class="feature"><b>Confidential space</b>Discuss real challenges openly within a trusted group.</div>
      <div class="feature"><b>Practical tools</b>Apply proven frameworks directly to your daily leadership.</div>
    </div>
    <div class="book">
      <div class="book__col"><h4>Limited spots available</h4>Each cohort is kept small to ensure depth, focus and personal attention for every member.</div>
      <div class="book__col"><h4>Book your free discovery call</h4>Speak with us to see if the group suits your goals.<br><span class="button">Book now</span></div>
    </div>
    <div class="accreditations" aria-label="Accrediting organisations">
      <span class="badge"></span><span class="badge badge--round"></span><span class="badge"></span><span class="badge badge--round"></span>
    </div>
  </section>

</main>
</body>
</html>
```